tinyTally Resource Book - 10 maths tasks to do outside

I need a 22 (11 pages back to back) page A6 sized book produced to standard for submission to professional printer. Needs to be as .pdf file showing guide lines and allowances for colour bleed. I have text already written and submitted as attachment in a Word file with margins set to A6 size. The theme of the materials is "Nature Play" so using lots of pictures from nature (Australia preferably) and showing lots of patterns in nature (rocks, leaves, flower petals etc). Some of the tasks refer to specific activities, such as "shadows" and "floating" so would be great to illustrate appropriately. The big emphasis is on learning outside the classroom, getting kids to engage actively with nature. I would like to see the pages as full colour - so not white background. The book itself will be spiral bound along the top edge so a margin of at least 1cm will be required at the top of each page (or the bottom of even numbered pages). Book will be printed on plastic laminated matte paper for outdoor use. Font size needs to be big enough to read. Fonts sizes, alignments and page numbers are all different at the moment and need to be standardised. One photo is included in a page as a sample if you can use it, otherwise disregard. Logo for Wattlebrook Numeracy Guild is also included to have as part of the acknowledgements at the back of the book.

Target Market(s)

Book is for early childhood and preschool teachers.

Industry/Entity Type

Education

Font styles to use
Sans Serif

Requirements
Must have
• Colour and appeal.
Nice to have
• Use of natural colours instead of bright catchy colours but that is your call.
Should not have
• American spelling

```html
<!DOCTYPE html>
<html lang="en-AU">
<head>
<meta charset="utf-8">
<title>tinyTally – How Many Leaves?</title>
<link rel="stylesheet" href="https://fonts.googleapis.com/css2?family=Fredoka:wght@600&family=Nunito:ital,wght@1,800&family=Questrial&display=swap">
<style>
  :root {
    --paper: #ffffff;
    --navy: #1f2a6e;
    --royal: #2b3a9c;
    --ink: #3a3a3a;
    --berry: #c8253a;
    --leaf-green: #a9c27a;
    --leaf-yellow: #e3d98c;
    --leaf-red: #c97a7a;
    --leaf-plum: #8f6a78;
    --wash: rgba(255, 255, 255, 0.55);
    --crop: #222222;
  }
  * { margin: 0; padding: 0; box-sizing: border-box; }
  html, body { width: 906px; height: 1200px; overflow: hidden; background: var(--paper); }
  .page { position: relative; width: 906px; height: 1200px; background: var(--paper); }

  .leaf-backdrop {
    position: absolute; left: 54px; top: 54px; width: 798px; height: 1091px;
    background:
      radial-gradient(circle at 15% 20%, var(--leaf-red) 0, transparent 22%),
      radial-gradient(circle at 80% 12%, var(--leaf-green) 0, transparent 25%),
      radial-gradient(circle at 30% 60%, var(--leaf-yellow) 0, transparent 28%),
      radial-gradient(circle at 85% 55%, var(--leaf-plum) 0, transparent 24%),
      radial-gradient(circle at 20% 90%, var(--leaf-green) 0, transparent 26%),
      radial-gradient(circle at 75% 92%, var(--leaf-red) 0, transparent 24%),
      linear-gradient(160deg, #b9c48a, #c99a8c 45%, #a7b87e);
  }
  .leaf-backdrop::after {
    content: ""; position: absolute; inset: 0; background: var(--wash);
  }

  .crop-marks { position: absolute; inset: 0; }

  .line { position: absolute; white-space: nowrap; }
  .task-title {
    left: 0; width: 906px; top: 140px; text-align: center;
    font: 600 48px/60px "Fredoka", sans-serif; color: var(--navy);
    text-shadow: 0 0 4px #fff, 0 0 4px #fff, 0 0 6px #fff;
  }
  .outcome {
    left: 0; width: 906px; text-align: center; padding-left: 50px;
    font: 600 31px/44px "Fredoka", sans-serif; color: var(--navy);
    text-shadow: 0 0 4px #fff, 0 0 4px #fff;
  }
  .subhead {
    left: 129px;
    font: italic 800 24px/30px "Nunito", sans-serif; color: var(--royal);
  }
  .body-text {
    left: 198px;
    font: 400 32px/43px "Questrial", sans-serif; color: var(--ink);
  }
  .bullet {
    left: 221px;
    font: 400 31px/38px "Questrial", sans-serif; color: var(--ink);
  }
  .bullet-mark {
    position: absolute; left: -28px; top: 11px; width: 15px; height: 15px;
    background: var(--berry); transform: rotate(45deg);
  }
  .page-number {
    position: absolute; left: 713px; top: 990px; width: 62px; height: 62px;
  }
</style>
</head>
<body>
<div class="page">
  <div class="leaf-backdrop" role="img" aria-label="Close-up photograph of scattered autumn leaves in green, yellow, red and plum tones"></div>

  <svg class="crop-marks" width="906" height="1200" viewBox="0 0 906 1200" aria-hidden="true">
    <g stroke="var(--crop)" stroke-width="1" fill="none">
      <path d="M0 75H42M75 0V42M0 54H42M54 0V42"/>
      <path d="M906 75H864M831 0V42M906 54H864M852 0V42"/>
      <path d="M0 1125H42M75 1200V1158M0 1145H42M54 1200V1158"/>
      <path d="M906 1125H864M831 1200V1158M906 1145H864M852 1200V1158"/>
    </g>
  </svg>

  <h1 class="line task-title">1. How Many Leaves?</h1>
  <p class="line outcome" style="top:214px">EYLF – Outcome 1:</p>
  <p class="line outcome" style="top:257px">Children have a strong sense</p>
  <p class="line outcome" style="top:301px">of identity</p>

  <p class="line subhead" style="top:367px">Children learn to interact in relation to others</p>
  <p class="line subhead" style="top:397px">with care, empathy and respect when they...</p>
  <p class="line body-text" style="top:440px">display awareness of and respect for</p>
  <p class="line body-text" style="top:483px">others’ perspectives</p>

  <p class="line subhead" style="top:536px">Educators promote this learning when</p>
  <p class="line subhead" style="top:568px">they...</p>
  <p class="line body-text" style="top:609px">organise learning environments</p>
  <p class="line body-text" style="top:651px">in ways that promote small group</p>
  <p class="line body-text" style="top:693px">interactions and play experiences</p>

  <p class="line subhead" style="top:748px">This task provides an opportunity to:</p>
  <p class="line bullet" style="top:796px"><span class="bullet-mark"></span>explore the concepts of “perspective”</p>
  <p class="line bullet" style="top:829px">and “comparing”</p>
  <p class="line bullet" style="top:870px"><span class="bullet-mark"></span>attempt the same task in different</p>
  <p class="line bullet" style="top:908px">ways</p>
  <p class="line bullet" style="top:949px"><span class="bullet-mark"></span>consider relationship between the</p>
  <p class="line bullet" style="top:992px">individual and the group</p>

  <svg class="page-number" viewBox="0 0 62 62" aria-label="Page 2">
    <polygon points="31,2 60,23 49,58 13,58 2,23" fill="var(--navy)"/>
    <text x="31" y="44" text-anchor="middle" fill="#ffffff" font-family="Fredoka, sans-serif" font-weight="600" font-size="28">2</text>
  </svg>
</div>
</body>
</html>
```